Advanced Therapeutic Massage Therapist

I need a business card advertising my massage services as an advanced therapeutic massage therapist. I offer advanced therapeutic massage, swedish and deep tissue. I want to create a simple, professional and feminine card. I like bright colours and creativity.

I prefer a bold and experimental approach rather than something status-quo. A card to suggest therapeutic healing through dynamic massage. Motifs, shapes or layout which suggest movement and flow.
Updates

Target Market(s)

Everybody!

Industry/Entity Type

Health And Wellness

Contact Information for Business Card

The card should include:
My name, logo, services offered and my contact details.

Sláine Dunleavy
Massage Therapist

- Swedish - Deep Tissue - Advanced Therapeutic

Phone: (+353) 87 216 4093
Email: regenerate@slainedunleavy-example.com
Website: www.slainedunlevy-example.com

Font styles to use
Serif
Sans Serif
Decorative
Script

Colors

Designer to choose colors to be used in the design.

Requirements
Must have
• An example may contain something like this, yet concise:
• "Sláine Dunleavy
• Massage Therapist
• - Swedish - Deep Tissue - Advanced Therapeutic"
Nice to have
• This sentence is optional:
• Imagery such as a logo or symbol. I have attached a file containing a logo I had produced however the name is incorrect now as it is "Sláine" not "Nelly". It could be edited to change it to Sláine.
• I have sent the file as .psd .jpg. .pdf and .png
• I like when the card conveys energy, movement, pressure points, flow etc.
• I just like the designer to follow their own style and ideas. I like bright colours but must have a lot of a base colour to offset it. I really prefer them to follow their own inspiration. That is my preference.
Should not have
• Pine trees, non-native trees to Britain and Ireland, exotic flowers or animals that are not native to Britain and Ireland.
• I don't like brown as the background colour of the card.
• The cars shouldn't look like a wedding invitation i.e too many floral type designs.

```html
<!DOCTYPE html>
<html lang="en">
<head>
<meta charset="utf-8">
<title>Sláine Dunleavy – Massage Therapist Business Card</title>
<link href="https://fonts.googleapis.com/css2?family=Great+Vibes&family=Quicksand:wght@400&family=Didact+Gothic&display=swap" rel="stylesheet">
<style>
  :root {
    --backdrop: #686868;
    --mint-light: #cdeee3;
    --mint-mid: #a8e0d0;
    --mint-deep: #8fd3c1;
    --ink-dark: #2c3a38;
    --charcoal: #232323;
    --charcoal-edge: #2b2b2b;
    --mint-text: #b5e6d8;
    --contact-text: #ededed;
    --gold-light: #f1d27a;
    --gold-deep: #b88a2f;
  }
  * { margin: 0; padding: 0; box-sizing: border-box; }
  html, body { width: 1200px; height: 550px; overflow: hidden; }
  body { background: var(--backdrop); position: relative; }

  .card {
    position: absolute;
    top: 158px;
    width: 390px;
    height: 234px;
    overflow: hidden;
  }

  /* Front */
  .card--front {
    left: 195px;
    background:
      radial-gradient(ellipse at 20% 30%, rgba(255,255,255,0.35), transparent 55%),
      radial-gradient(ellipse at 80% 75%, rgba(143,211,193,0.45), transparent 60%),
      linear-gradient(135deg, var(--mint-light), var(--mint-mid) 60%, var(--mint-deep));
  }
  .front__emblem {
    position: absolute;
    left: 139px; top: 44px;
    width: 112px; height: 112px;
    border-radius: 50%;
    background: radial-gradient(circle, var(--gold-light), var(--gold-deep) 75%, rgba(184,138,47,0.6));
    opacity: 0.85;
  }
  .front__name {
    position: absolute;
    left: 0; width: 100%;
    top: 158px;
    text-align: center;
    font-family: "Great Vibes", cursive;
    font-size: 24px;
    color: var(--ink-dark);
    line-height: 1;
  }
  .front__role {
    position: absolute;
    left: 0; width: 100%;
    top: 182px;
    text-align: center;
    font-family: "Quicksand", sans-serif;
    font-size: 9px;
    letter-spacing: 0.6px;
    color: var(--ink-dark);
  }

  /* Back */
  .card--back {
    left: 614px;
    background: linear-gradient(160deg, var(--charcoal-edge), var(--charcoal));
  }
  .back__emblem {
    position: absolute;
    left: 236px; top: 2px;
    width: 232px; height: 232px;
    border-radius: 50%;
    background: radial-gradient(circle, var(--gold-light), var(--gold-deep) 80%);
  }
  .back__name {
    position: absolute;
    left: 14px; top: 24px;
    font-family: "Great Vibes", cursive;
    font-size: 30px;
    color: var(--mint-text);
    line-height: 1;
    z-index: 1;
  }
  .back__role {
    position: absolute;
    left: 20px; top: 57px;
    font-family: "Quicksand", sans-serif;
    font-size: 12px;
    letter-spacing: 0.8px;
    color: var(--contact-text);
  }
  .contact-list {
    position: absolute;
    left: 20px; top: 153px;
    list-style: none;
    font-family: "Didact Gothic", sans-serif;
    font-size: 10.5px;
    letter-spacing: -0.1px;
    color: var(--contact-text);
    z-index: 1;
  }
  .contact-list li {
    display: flex;
    align-items: center;
    height: 17px;
    white-space: nowrap;
  }
  .contact-list svg {
    width: 9px; height: 9px;
    margin-right: 9px;
    flex: none;
    fill: var(--mint-text);
  }
  .back__services {
    position: absolute;
    left: 20px; top: 209px;
    font-family: "Didact Gothic", sans-serif;
    font-size: 11.5px;
    color: var(--mint-text);
    white-space: nowrap;
    z-index: 1;
  }
</style>
</head>
<body>

<section class="card card--front">
  <div class="front__emblem" role="img" aria-label="Gold circular tree emblem"></div>
  <p class="front__name">Sláine Dunleavy</p>
  <p class="front__role">massage therapist</p>
</section>

<section class="card card--back">
  <div class="back__emblem" role="img" aria-label="Large gold circular tree emblem"></div>
  <p class="back__name">Sláine Dunleavy</p>
  <p class="back__role">massage therapist</p>
  <ul class="contact-list">
    <li>
      <svg viewBox="0 0 10 10" aria-hidden="true"><path d="M1 3.2C1 2 2.5 1.5 5 1.5S9 2 9 3.2V4H7V3H3v1H1z M2.5 4.5h5L8.5 8.5h-7z"/></svg>
      (+353) 87 216 4093
    </li>
    <li>
      <svg viewBox="0 0 10 10" aria-hidden="true"><rect x="0.5" y="2" width="9" height="6"/><path d="M0.5 2L5 5.5 9.5 2" fill="none" stroke="#232323" stroke-width="0.9"/></svg>
      regenerate@slainedunleavy-example.com
    </li>
    <li>
      <svg viewBox="0 0 10 10" aria-hidden="true"><circle cx="5" cy="5" r="4.5"/><path d="M0.5 5h9M5 0.5v9M2 2.5q3 1.5 6 0M2 7.5q3-1.5 6 0" stroke="#232323" stroke-width="0.7" fill="none"/></svg>
      www.slainedunlevy-example.com
    </li>
  </ul>
  <p class="back__services">Swedish - Deep Tissue - Advanced Therapeutic</p>
</section>

</body>
</html>
```